Market Compass Web Design

The marketcompassly.com web site will be the source for unbiased economic performance expectations directly from the voice of business owners. Our Market Compass survey effectively asks business owners "How's business?" The web site will present the resultant survey data, graphs, and reports to bankers and business owners. The overall goal is to help bankers better understand businesses of various sizes and industry types, as well as the direction in which our economy is heading by supplying them with the most current possible data.
Updates

Changes have been made to our list of requirements (and list of things the site should NOT include) so please review the briefing again. Thanks!

Reminder: the final deadline for this project isĀ Saturday, February 18, 2012 3:59 AM! Please get your submissions in by that time!

Target Market(s)

Bankers and Business Owners

Industry/Entity Type

Business

Requirements
Must have
• CSS stylesheet, incorporation an Market Compass logo (could be based on the attached example, but rebranding is encouraged), intuitive navigation scheme based on the supplied flow chart, space to incorporate additional sponsor branding and/or advertising in the future
Nice to have
• Space to integrate Google Charts for the graphs representing research data
Should not have
• Incorporated elements from Corvane Insights's main company website - the branding, look, feel, navigation and content of the Market Compass Web site should be completely different and independent

```html
<!DOCTYPE html>
<html lang="en">
<head>
<meta charset="utf-8">
<title>Market Compass</title>
<link href="https://fonts.googleapis.com/css2?family=Source+Sans+3:wght@400;600;700&display=swap" rel="stylesheet">
<style>
:root{
  --navy:#2b2f80;
  --ink:#3b3f8c;
  --nav-top:#4449a6;
  --nav-bottom:#2a2e8c;
  --nav-active:#23287a;
  --panel-top:#f4f6fc;
  --panel-bottom:#dfe5f5;
  --line:#d8dcea;
  --footer:#112072;
  --footer-deep:#0c1a63;
  --muted:#6b6f8f;
  --white:#ffffff;
}
*{box-sizing:border-box;margin:0;padding:0}
html,body{width:912px;height:1200px;overflow:hidden}
body{position:relative;background:var(--white);font-family:"Source Sans 3",sans-serif;color:var(--ink);font-size:10.5px;line-height:15px}
a{color:inherit;text-decoration:none}
.abs{position:absolute}

.utility-bar{left:0;top:0;width:912px;height:22px;background:linear-gradient(#ffffff,#f1f2f7)}
.utility-links{right:45px;top:5px;font-size:10px;color:var(--ink)}
.utility-links span{margin:0 4px;color:#999}

.brand{left:28px;top:52px;display:flex;align-items:center;gap:10px}
.brand-mark{width:26px;height:26px;background:var(--navy)}
.brand-name{font-size:30px;font-weight:400;color:var(--navy);letter-spacing:.5px}

.connect{left:712px;top:63px;display:flex;align-items:center;gap:5px;font-size:13px;color:var(--ink)}
.connect .arrow{color:#999;font-size:10px;margin-right:6px}
.social{display:inline-block;width:15px;height:15px;background:var(--navy);margin-left:2px}
.search{left:680px;top:102px;width:208px;height:22px;border:2px solid #9fa6c5;border-radius:2px;background:#fff;font-size:10px;color:#999;padding:2px 7px}
.search svg{position:absolute;right:5px;top:2px}

.main-nav{left:0;top:149px;width:912px;height:36px;background:linear-gradient(var(--nav-top),var(--nav-bottom));display:flex;padding-left:17px}
.main-nav a{height:36px;display:flex;align-items:center;justify-content:center;color:#fff;font-size:14px;border-right:1px solid rgba(255,255,255,.35)}
.main-nav a.active{background:var(--nav-active);border-right:none;position:relative}
.main-nav a.active::after{content:"";position:absolute;bottom:0;left:47px;border:5px solid transparent;border-bottom-color:#fff}
.main-nav a:last-child{border-right:none}

.hero{left:15px;top:190px;width:584px;height:284px;border:1px solid #c9cde0;background:linear-gradient(120deg,#c7d3e8 0%,#eef1f7 40%,#e9d7c4 65%,#9fb4d6 100%)}
.hero-caption{left:2px;top:130px;width:412px;height:67px;background:rgba(255,255,255,.78);padding:8px 15px}
.hero-caption h2{font-size:15px;font-weight:400;color:var(--navy);text-transform:uppercase;margin-bottom:3px}
.hero-caption h2 b{font-weight:700}
.hero-caption p{font-size:10.5px;line-height:15px}
.hero-next{right:12px;top:88px}

.promo{left:604px;top:190px;width:288px;height:284px;border-radius:8px;background:linear-gradient(var(--panel-top),var(--panel-bottom));padding:22px 22px}
.promo h2{font-size:18px;font-weight:400;color:var(--navy);line-height:22px;margin-bottom:10px}
.promo p{font-size:10.5px;line-height:15px;margin-bottom:3px}
.btn{display:inline-block;border:1px solid #b7bcd2;border-radius:12px;background:#fff;font-size:10px;padding:3px 11px;color:var(--ink)}
.promo .btn{margin-top:5px}
.dots{right:16px;bottom:14px;display:flex;gap:5px}
.dots i{width:11px;height:11px;background:var(--navy)}

.section-title{font-size:15px;font-weight:400;color:var(--navy);text-transform:uppercase}
.section-title b{font-weight:700}

.welcome{left:19px;top:503px;width:572px}
.welcome .section-title{margin-bottom:10px}
.welcome p{margin-bottom:1px}

.divider{left:604px;top:495px;width:1px;height:525px;background:linear-gradient(var(--line),#fff)}

.news{left:621px;top:503px;width:268px}
.news .section-title{margin-bottom:11px}
.news-item{margin-bottom:9px}
.news-item .date{font-weight:700;color:var(--navy);margin-top:2px}
.view-all{display:block;border-bottom:2px solid transparent;border-image:linear-gradient(90deg,var(--navy),#fff) 1;background:linear-gradient(90deg,#eceef5,#fff);font-size:10px;padding:1px 4px;text-transform:uppercase}

.calendar{left:619px;top:806px;width:270px}
.calendar .section-title{margin-bottom:12px}
.event{padding-left:3px}
.event .date{font-size:10px;font-weight:600;color:var(--navy);margin-bottom:1px}
.event .tag{display:block;margin:1px 0 4px auto;width:max-content;font-size:8.5px;background:#e6e8ef;padding:0 6px;line-height:13px;text-transform:uppercase}

.card{top:698px;width:271px;height:288px;border-radius:7px;background:linear-gradient(var(--panel-top),#fff 60%,#eef1f8);box-shadow:0 0 3px rgba(0,0,0,.12)}
.card-head{height:40px;border-radius:7px 7px 0 0;background:linear-gradient(#fbfbfd,#eceef4);display:flex;align-items:center;justify-content:space-between;padding:0 16px}
.card-head svg{flex:none}
.card .visual{position:absolute}
.card h4{font-size:10.5px;font-weight:700;color:var(--navy)}
.card .cta{position:absolute;font-size:12px;text-transform:uppercase;color:var(--navy)}
.card .cta b{font-weight:700}

.footer{left:0;top:1052px;width:912px;height:148px;background:linear-gradient(var(--footer),var(--footer-deep));color:#fff}
.footer-connect{left:27px;top:23px;font-size:12.5px;display:flex;align-items:center;gap:3px}
.footer-connect .social{background:#fff;width:14px;height:14px}
.footer-connect span:first-child{margin-right:8px}
.footer-social{left:27px;top:46px;font-size:10px}
.footer-nav{right:36px;top:18px;font-size:12.5px}
.footer-nav span,.footer-social span{margin:0 7px}
.footer-legal{right:27px;top:56px;font-size:10px;text-align:right;line-height:18px}
</style>
</head>
<body>

<header>
  <div class="abs utility-bar"></div>
  <nav class="abs utility-links"><a href="#">Register</a><span>|</span><a href="#">Sitemap</a><span>|</span><a href="#">Member Login</a></nav>

  <a class="abs brand" href="#"><i class="brand-mark"></i><span class="brand-name">Market Compass</span></a>

  <div class="abs connect">Connect With <span class="arrow">›</span>
    <i class="social"></i><i class="social"></i><i class="social"></i><i class="social"></i>
  </div>
  <div class="abs search">type your word here
    <svg width="16" height="14" viewBox="0 0 16 14"><circle cx="6" cy="6" r="4.5" fill="none" stroke="#999" stroke-width="1.5"/><line x1="9.5" y1="9" x2="14" y2="13" stroke="#999" stroke-width="2"/></svg>
  </div>

  <nav class="abs main-nav">
    <a class="active" href="#" style="width:103px">Home</a>
    <a href="#" style="width:156px">Graphs &amp; Data</a>
    <a href="#" style="width:107px">Info</a>
    <a href="#" style="width:125px">Sponsors</a>
    <a href="#" style="width:130px">GetMore</a>
  </nav>
</header>

<main>
  <section class="abs hero" role="img" aria-label="Photo of a woman typing on a laptop">
    <div class="abs hero-caption">
      <h2><b>Company</b> punch lines goes here..</h2>
      <p>To manage the static website HTML knowledge is the required. The simple website are also said as the static web as its embedded on a page.</p>
    </div>
    <svg class="abs hero-next" width="30" height="110" viewBox="0 0 30 110"><polyline points="2,2 28,55 2,108" fill="none" stroke="#fff" stroke-width="1.5"/></svg>
  </section>

  <aside class="abs promo">
    <h2>Update your Profile and Have Lunch on Us!</h2>
    <p>We have learnt that designing is not only inclined to powerful imaginations but also focused and attractive to expected viewers also.</p>
    <p>At Brightmesh Solutions we use all the latest tech-nologies for web designing. Brightmesh Solutions provides the best web designing which compels the customers to ask and inquire about. We ensure that our designs represent the client area to perfection and look convincing to the targeted audience as well.</p>
    <a class="btn" href="#">CLICK HERE TO VIEW MORE</a>
    <div class="abs dots"><i></i><i></i><i></i><i></i></div>
  </aside>

  <section class="abs welcome">
    <h1 class="section-title">Welcome to <b>Market Compass</b></h1>
    <p>E-Commerce is a major progress in technology that has changed the way in which the customers now purchase information, products and the services. It’s the new way of providing an opportunity to make your products and services available in the global market 24 hours a day through Internet</p>
    <p>Brightmesh Solutions is specialized in handling advanced web projects and the ongoing projects that require permanent maintenance and support .We like challenges and do complete these challenge with expertise we like solving questions that arises in such projects as these helps us to grow also. When considering advanced web development project, finding the right answers to the hard questions is a challenge for any firm, it includes expertise and enables Brightmesh Solutions to specialize in advanced projects and ongoing projects that require permanent support and maintenance.</p>
  </section>

  <div class="abs divider"></div>

  <section class="abs news">
    <h2 class="section-title">In the <b>News</b></h2>
    <article class="news-item"><p>Brightmesh Solutions to specialize in advanced projects and ongoing projects that require permanent support and maintenance.</p><p class="date">Posted on 25.Jan.2012</p></article>
    <article class="news-item"><p>Brightmesh Solutions to specialize in advanced projects and ongoing projects that require permanent support and maintenance.</p><p class="date">Posted on 25.Jan.2012</p></article>
    <article class="news-item"><p>Brightmesh Solutions to specialize in advanced projects and ongoing projects that require permanent support and maintenance.</p><p class="date">Posted on 25.Jan.2012</p></article>
    <a class="view-all" href="#">View all</a>
  </section>

  <section class="abs calendar">
    <h2 class="section-title">View by <b>Calender</b></h2>
    <div class="event"><p class="date">FEB,25,2012</p><p>Brightmesh Solutions to specialize in advanced projects and ongoing projects</p><span class="tag">Register</span></div>
    <div class="event"><p class="date">FEB,25,2012</p><p>Brightmesh Solutions to specialize in advanced projects and ongoing projects</p><span class="tag">Register</span></div>
    <a class="view-all" href="#" style="margin-top:10px">View all</a>
  </section>

  <section class="abs card" style="left:13px">
    <div class="card-head"><h2 class="section-title">Know market <b>Status</b></h2>
      <svg width="10" height="12" viewBox="0 0 10 12"><polyline points="2,1 8,6 2,11" fill="none" stroke="#bbb" stroke-width="2.5"/></svg></div>
    <div class="visual" role="img" aria-label="Pen resting on a stock market chart" style="left:16px;top:50px;width:229px;height:80px;border:2px solid #c8d0ec;background:linear-gradient(110deg,#eef0f8,#c9cfe8 50%,#f1e8ee)"></div>
    <div class="abs" style="left:17px;top:144px;width:240px">
      <h4>Earn $52 Gift Card For Subrise?</h4>
      <p>Static website are cheaper and also it needs less maintenance too. It’s the simplest, cheapest and also the basic thing the search engine picks it up very easily. We at Brightmesh provide you the best simple websites</p>
    </div>
    <a class="cta" href="#" style="left:16px;top:250px">Click here to <b>Update profile</b></a>
  </section>

  <section class="abs card" style="left:295px">
    <div class="card-head"><h2 class="section-title">Featured <b>Graphs</b></h2>
      <svg width="10" height="12" viewBox="0 0 10 12"><polyline points="2,1 8,6 2,11" fill="none" stroke="#bbb" stroke-width="2.5"/></svg></div>
    <div class="visual" role="img" aria-label="Map of the United States shaded by region" style="left:30px;top:58px;width:185px;height:110px;border-radius:20px;background:linear-gradient(90deg,#c9c9cc 0%,#c9c9cc 35%,#3b4bc4 40%,#3b4bc4 75%,#8a8a90 100%)"></div>
    <div class="abs" style="left:26px;top:182px;width:240px">
      <h4>Earn $52 Gift Card For Subrise?</h4>
      <p>Static website are cheaper and also it needs less maintenance too. It’s the simplest, cheapest and also the basic thing the search engine</p>
    </div>
    <a class="cta" href="#" style="left:27px;top:251px">Click here to <b>View more</b></a>
  </section>
</main>

<footer class="abs footer">
  <div class="abs footer-connect"><span>Connect With Us</span><i class="social"></i><i class="social"></i><i class="social"></i><i class="social"></i></div>
  <div class="abs footer-social"><a href="#">Friendsy</a><span>|</span><a href="#">Linkwork</a><span>|</span><a href="#">Chirper</a><span>|</span><a href="#">Viewtube</a></div>
  <nav class="abs footer-nav"><a href="#">Home</a><span>|</span><a href="#">Graphs &amp; Data</a><span>|</span><a href="#">Info</a><span>|</span><a href="#">Sponsors</a><span>|</span><a href="#">GetMore</a><span>|</span><a href="#">Contact Us</a></nav>
  <div class="abs footer-legal">Copyright © 2012 Company Nam &nbsp;|&nbsp; All right reserved<br>Terms &amp; Condition &nbsp;|Privacy Policy</div>
</footer>

</body>
</html>
```